Zvo Klinieken website for a maxillofacial surgery clinic

It's a website for a clinic for maxillofacial surgery in WordPress . The website doesn't need to be complicated but has to look professional. It needs to be in Dutch so i can give the texts. Similar websites are www.tandartsenpraktijkveldorm.nl or www.pbtspecialisten.nl. Pages would be sort of similar to https://hetcentrumvoorgezichtszorg.nl/ or https://wervelmondclinics.nl/. Those lasts are maxillofacial surgery clinic websites, but there are little more extensive.
I uploaded the logo. If this is not the proper quality i can upload the eps. Logo was made through pixelforum.

Target Market(s)

Patients who can find me and see information about the clinic

Industry/Entity Type

Healthcare

Coding

Coded - Design and coding required

Number of Pages Required

5+ page

Font styles to use
Other font styles liked:
• Something standard professional

Colors
0054AA
0677BA
7BADD7
CADEEF
E8F1F8

Requirements
Nice to have
• Something in line with the logo. I prefer a little dark like the darker logos but I'm not sure if that's professional. Logos bkvzo and rlpw are instances i'm registered to so they will have to be on the website too but small somewhere.

```html
<!DOCTYPE html>
<html lang="nl">
<head>
<meta charset="utf-8">
<title>Zvo Klinieken – Kliniek voor Maxillofaciale Chirurgie</title>
<link href="https://fonts.googleapis.com/css2?family=Poppins:wght@300;400;500;600;700&display=swap" rel="stylesheet">
<style>
:root{
  --slate:#6e82a5;
  --slate-dark:#5f7396;
  --blue:#35a7e0;
  --blue-deep:#1f8fd0;
  --ink:#111;
  --text:#333;
  --grey-bg:#f3f3f3;
  --card-bg:#e3e9f1;
  --white:#fff;
}
*{margin:0;padding:0;box-sizing:border-box}
html,body{width:1200px;height:4559px;overflow:hidden}
body{font-family:"Poppins",sans-serif;color:var(--text);background:var(--white);position:relative}
.abs{position:absolute}
a{color:inherit;text-decoration:none}

/* top bar */
.topbar{left:0;top:0;width:1200px;height:54px;background:var(--slate);color:#fff;font-size:13px}
.topbar span{position:absolute;top:17px}
.topbar b{font-weight:600}

/* hero */
.hero{left:0;top:54px;width:1200px;height:680px;overflow:hidden}
.hero-photo{position:absolute;inset:0;background:linear-gradient(100deg,#3f9fcf 0%,#57acd3 40%,#a8c7d6 62%,#e7d5c6 78%,#c8b4a2 100%)}
.nav{top:80px;font-size:14px;font-weight:500;color:#fff}
.logo-badge{left:485px;top:-30px;width:230px;height:230px;border-radius:50%;background:#fff;display:flex;align-items:center;justify-content:center}
.brand{font-family:"Poppins",sans-serif;font-weight:600;color:var(--slate);font-size:26px;letter-spacing:.5px}
.hero-welcome{left:110px;top:252px;color:#fff;font-size:25px;font-weight:300}
.hero h1{position:absolute;left:110px;top:292px;color:#fff;font-size:34px;font-weight:600;line-height:43px;width:520px}
.hero-text{left:112px;top:390px;color:#fff;font-size:16px;line-height:28px;width:470px;font-weight:300}
.btn{display:inline-block;border-radius:22px;font-size:15px;padding:0 24px;height:40px;line-height:40px}
.btn-white{background:#fff;color:#333}
.btn-blue{background:var(--blue);color:#fff}

/* section titles */
.sec-title{width:1200px;text-align:center;font-size:40px;font-weight:700;color:var(--ink)}

/* about */
.about-panel{left:112px;top:988px;width:976px;height:313px;background:var(--slate);border-radius:8px}
.about-photo{left:133px;top:942px;width:368px;height:408px;border-radius:6px;background:linear-gradient(160deg,#dce6ee,#b9cad8 60%,#eef2f5);box-shadow:0 6px 18px rgba(0,0,0,.15)}
.about-text{left:523px;top:1020px;width:545px;color:#fff;font-size:13.5px;line-height:28px;font-weight:300}

/* services */
.services{left:0;top:1451px;width:1200px;height:641px;background:var(--grey-bg)}
.svc-sub{left:270px;top:1629px;width:660px;text-align:center;font-size:16.5px;line-height:30px;color:#333}
.svc{top:1717px;width:301px;height:306px;text-align:center}
.svc.active{background:var(--card-bg)}
.svc-icon{width:96px;height:96px;border-radius:50% 50% 46% 46%;background:var(--blue);margin:18px auto 0}
.svc.active .svc-icon{background:transparent;border:5px solid var(--slate)}
.svc h3{margin-top:26px;font-size:16px;font-weight:400;color:var(--blue)}
.svc p{margin:14px auto 0;width:270px;font-size:14px;line-height:28px;color:#333}
.arrow{top:1829px;width:40px;height:40px;border-radius:50%}

/* visit */
.visit h2{position:absolute;left:110px;top:2195px;font-size:42px;font-weight:700;line-height:56px;color:var(--ink);width:520px}
.visit-text{left:110px;top:2322px;width:460px;font-size:14px;line-height:28.5px;color:#333}
.visit-photo{left:692px;top:2200px;width:345px;height:340px;border-radius:30px;background:linear-gradient(135deg,#9cc8ea,#4d93cf 55%,#2e6fae);transform:rotate(3deg);box-shadow:-8px 8px 0 #2f7fc2}

/* gallery */
.gallery-bg{left:0;top:2648px;width:1200px;height:317px;background:var(--grey-bg)}
.g-item{border-radius:14px;overflow:hidden}
.g-big{left:112px;top:2853px;width:433px;height:344px;background:linear-gradient(135deg,#4a7b98,#26455d 60%,#1b3040);box-shadow:-12px 10px 0 var(--blue-deep)}
.g-a{left:558px;top:2853px;width:258px;height:166px;background:var(--blue)}
.g-b{left:828px;top:2853px;width:259px;height:166px;background:linear-gradient(135deg,#dfe8ef,#c9d6df)}
.g-c{left:558px;top:3031px;width:258px;height:166px;background:linear-gradient(135deg,#e9eef2,#cfdae3)}
.g-d{left:828px;top:3031px;width:259px;height:166px;background:linear-gradient(135deg,#d6e4ee,#a9c4d8)}

/* contact */
.map-back{left:55px;top:3380px;width:500px;height:570px;border-radius:14px;background:#8cc6ec;transform:rotate(-4deg)}
.map{left:88px;top:3390px;width:478px;height:566px;background:linear-gradient(135deg,#b8dcf4 0%,#b8dcf4 30%,#f4f09a 45%,#f4f09a 100%)}
.contact h2{position:absolute;left:627px;top:3412px;font-size:41px;font-weight:700;color:var(--ink)}
.field{left:598px;width:490px;height:55px;border:1.5px solid #555;border-radius:28px;font-size:13px;color:#333;padding:19px 0 0 20px}
.field.msg{height:138px;border-radius:22px}

/* footer */
.footer{left:0;top:3990px;width:1200px;height:569px}
.foot-col{top:4226px;color:#fff}
.foot-col h4{font-size:16px;font-weight:500;margin-bottom:16px}
.foot-col li{list-style:none;font-size:13px;line-height:31px;font-weight:300}
.social{top:4476px;width:26px;height:26px;border-radius:50%;border:2px solid #fff}
.copy{left:0;top:4515px;width:1200px;text-align:center;color:#fff;font-size:11px;font-weight:300}
</style>
</head>
<body>

<div class="abs topbar">
  <span style="left:112px"><b>Plaats:</b> Lorem Ipsum, NED</span>
  <span style="left:860px"><b>Bel Ons Vandaag:</b> +(888)888 8888</span>
</div>

<section class="abs hero">
  <div class="hero-photo" role="img" aria-label="Glimlachende patiënte in de behandelstoel bij de tandarts"></div>
  <svg class="abs" style="left:0;top:0" width="1200" height="680" viewBox="0 0 1200 680">
    <path d="M0 480 C180 600 420 680 650 660 C880 640 1060 580 1200 540 L1200 680 L0 680Z" fill="#fff"/>
    <path d="M0 480 C180 620 420 690 650 667 C880 646 1060 582 1200 520 L1200 547 C1060 600 880 660 650 680 C420 700 180 620 0 480Z" fill="var(--blue-deep)"/>
  </svg>
</section>

<a class="abs nav" style="left:112px">Thuis</a>
<a class="abs nav" style="left:229px">Over Ons</a>
<a class="abs nav" style="left:374px">Diensten</a>
<a class="abs nav" style="left:845px">Getuigenissen</a>
<a class="abs nav" style="left:1027px">Contact</a>
<div class="abs logo-badge"><span class="brand">Zvo Klinieken</span></div>

<p class="abs hero-welcome">Welkom bij</p>
<div class="hero"><h1 style="top:292px">kliniek Voor Maxillofaciale Chirurgie.</h1></div>
<p class="abs hero-text">Lorem ipsum dolor sit amet, consectetur adipiscing elit, sed do eiusmod temporpsum dolor sit amet,</p>
<a class="abs btn btn-white" style="left:112px;top:453px">Afspraak aanvragen</a>

<h2 class="abs sec-title" style="left:0;top:815px">Over Ons</h2>
<div class="abs about-panel"></div>
<div class="abs about-photo" role="img" aria-label="Twee artsen in witte jassen naast elkaar"></div>
<p class="abs about-text">Lorem ipsum dolor sit amet, consectetur adipiscing elit, sed do eiusmod tempor incididunt ut labore et dolore magna aliqua. Quis ipsum suspendisse avida. isus commodo viverra maecenas accumsan lacus vel facilisis.onsectetu­radipiscing lit, sed do eiusmod tempor incididunt ut labore et dolore magna aliqua. Quis psum suspendisse ultrices gravida. Risus commodo viverra maecenas ccumsan lacust vel facilisis. Lorem ipsum dolor sit amet, consectetur adipiscing elit, sed do mod tempor incididunt ut labore et dolore magna aliqua.</p>
<a class="abs btn btn-blue" style="left:523px;top:1229px;height:38px;line-height:38px;font-size:14px">Lees verder</a>

<section class="abs services"></section>
<h2 class="abs sec-title" style="left:0;top:1527px">Onze Diensten</h2>
<p class="abs svc-sub">Lorem ipsum dolor sit amet, consectetur adipiscing elit, sed do eiusmod tempor incididunt ut labore et dolore magna aliqua.</p>
<div class="abs arrow" style="left:46px;background:var(--blue)"><svg width="40" height="40"><path d="M23 12 L15 20 L23 28" stroke="#fff" stroke-width="3" fill="none"/></svg></div>
<div class="abs arrow" style="left:1110px;background:#b9dcf1"><svg width="40" height="40"><path d="M17 12 L25 20 L17 28" stroke="#fff" stroke-width="3" fill="none"/></svg></div>
<div class="abs svc" style="left:91px"><div class="svc-icon"></div><h3>Maxillofaciale Chirurgie</h3><p>Lorem ipsum dolor sit amet, nsectetur adipiscing elit, sed do eiusmod tempor incididunt ut labore et dolore magna aliqua.</p></div>
<div class="abs svc active" style="left:451px"><div class="svc-icon"></div><h3>VERWIJSPRAKTIJK</h3><p>Lorem ipsum dolor sit amet, nsectetur adipiscing elit, sed do eiusmod tempor incididunt ut labore et dolore magna aliqua.</p></div>
<div class="abs svc" style="left:810px"><div class="svc-icon"></div><h3>VERWIJZER</h3><p>Lorem ipsum dolor sit amet, nsectetur adipiscing elit, sed do eiusmod tempor incididunt ut labore et dolore magna aliqua.</p></div>

<section class="visit">
  <h2>Bezoek Ons Vandaag Nog!</h2>
  <p class="abs visit-text">iusmod tempor incididunt ut labore et dolore uspendisse ultrices gravida. Risus commodo viverra maecenas lfacilisis.ultrices avida. Risus commodo viverra maecenas accumsan lacus vel cilisis.Risus commodo viverra maecenas lfacilisis.ultrices avida. Risus mmodo viverra maecenas accumsan lacus vel facilisis.</p>
  <a class="abs btn btn-blue" style="left:112px;top:2470px;font-size:14px">Lees verder</a>
  <div class="abs visit-photo" role="img" aria-label="Lichte behandelkamer met tandartsstoel"></div>
</section>

<div class="abs gallery-bg"></div>
<h2 class="abs sec-title" style="left:0;top:2699px">Onze galerij</h2>
<div class="abs g-item g-big" role="img" aria-label="Chirurg met mondkapje tijdens een operatie">
  <svg class="abs" style="left:196px;top:152px" width="40" height="40"><circle cx="20" cy="20" r="19" fill="#fff"/><circle cx="20" cy="20" r="15" fill="var(--blue)"/><path d="M16 13 L27 20 L16 27Z" fill="#fff"/></svg>
</div>
<div class="abs g-item g-a" role="img" aria-label="Patiënte bij de tandarts met blauwe overlay">
  <svg class="abs" style="left:116px;top:70px" width="26" height="26"><circle cx="11" cy="11" r="7" stroke="#fff" stroke-width="3" fill="none"/><path d="M16 16 L23 23" stroke="#fff" stroke-width="3"/></svg>
</div>
<div class="abs g-item g-b" role="img" aria-label="Lachende vrouw in de tandartsstoel"></div>
<div class="abs g-item g-c" role="img" aria-label="Lachende patiënte in de behandelkamer"></div>
<div class="abs g-item g-d" role="img" aria-label="Patiënte tijdens een tandheelkundig onderzoek"></div>
<a class="abs btn btn-blue" style="left:540px;top:3222px;font-size:14px;height:38px;line-height:38px">Bekijk meer</a>

<div class="abs map-back"></div>
<div class="abs map" role="img" aria-label="Kaart van Nederland met de locatie van de kliniek"></div>
<section class="contact">
  <h2>Contact Formulier</h2>
  <div class="abs field" style="top:3547px">Naam</div>
  <div class="abs field" style="top:3616px">E-mail</div>
  <div class="abs field" style="top:3685px">Telefoon nr</div>
  <div class="abs field msg" style="top:3754px">Tekst hier...</div>
  <a class="abs btn btn-blue" style="left:598px;top:3909px;font-size:14px">Bekijk meer</a>
</section>

<footer class="abs footer">
  <svg class="abs" style="left:0;top:0" width="1200" height="569" viewBox="0 0 1200 569">
    <path d="M0 150 C300 30 900 30 1200 150 L1200 569 L0 569Z" fill="var(--slate)"/>
    <path d="M0 150 C300 30 900 30 1200 150" stroke="var(--blue-deep)" stroke-width="5" fill="none"/>
  </svg>
  <div class="abs" style="left:0;top:120px;width:1200px;text-align:center"><span class="brand" style="color:#fff;font-size:40px">Zvo Klinieken</span></div>
</footer>
<div class="abs foot-col" style="left:156px"><h4>Snelle koppelingen</h4><ul><li>Thuis</li><li>Over Ons</li><li>Diensten</li><li>Getuigenissen</li><li>Contact</li></ul></div>
<div class="abs foot-col" style="left:386px"><h4>Kaakchirurgie</h4><ul><li>Behandelingen</li><li>Implantologie</li><li>Informatiefolders</li><li>Wachttijden</li><li>Kaak- en Tandklachten</li><li>Veel gestelde vragen</li></ul></div>
<div class="abs foot-col" style="left:607px"><h4>Neem contact met ons op</h4><ul>
  <li><svg width="12" height="14"><path d="M6 1 C3 1 1 3 1 6 C1 9 6 13 6 13 C6 13 11 9 11 6 C11 3 9 1 6 1Z" fill="#fff"/><circle cx="6" cy="6" r="2" fill="var(--slate)"/></svg> Lorem Ipsum, NED</li>
  <li><svg width="12" height="12"><path d="M2 1 L5 1 L6 4 L4 5 C5 7 6 8 8 9 L9 7 L12 8 L12 11 C6 11 1 6 1 1Z" fill="#fff"/></svg> +1(888)888 8888</li>
  <li style="line-height:20px;margin-top:6px"><svg width="13" height="11"><rect x="1" y="1" width="11" height="9" fill="#fff"/><path d="M1 1 L6.5 6 L12 1" stroke="var(--slate)" fill="none"/></svg> info@zvoklinieken.nl</li></ul></div>
<div class="abs foot-col" style="left:899px"><h4>Informatie</h4><ul><li>Behandelingen</li><li>Informatiebrochures</li><li>Intake plannen</li><li>Wachttijden</li><li>Veel Gestelde Vragen</li></ul></div>
<div class="abs social" style="left:545px"></div>
<div class="abs social" style="left:587px"></div>
<div class="abs social" style="left:629px"></div>
<p class="abs copy">© 2023 Zvo Klinieken | All Rights Reserved</p>

</body>
</html>
```